Contemporary new French wine brand needs logo and series of label design

to design a new contemporary logo and series of labels for a new French wine brand. We hope to attract not just current French wine drinkers but new ones who may appreciate a less traditional and more modern style.
Updates

Reason: we are wanting to extend the project for a few days more to receive more submissions since we had fewer designs submitted than we were expecting, maybe because of the holidays.

Target Market(s)

people who follow the arts community (eg. music, theatre, visual/video arts, dance) --- all mature ages.

Industry/Entity Type

French Wine

Requirements
Must have
• a clear, memorable treatment for the name MORIVAL with accompanying logo.
Nice to have
• embossing, matte/gloss refinement, tasteful foil stamping, coated stock for the whites to help the integrity of the paper in and out of ice buckets. A combo of say, three types of fonts; a semi custom font for the brand name Morival and maybe a script and one other.
Should not have
• not traditional French

```html
<!DOCTYPE html>
<html lang="fr">
<head>
<meta charset="utf-8">
<title>Morival — Sauvignon Blanc</title>
<link href="https://fonts.googleapis.com/css2?family=Tinos:wght@400&family=Open+Sans:wght@400&display=swap" rel="stylesheet">
<style>
  :root {
    --paper: #ffffff;
    --backdrop: #ffffff;
    --ink: #1d1a1c;
    --berry: #c3447f;
    --berry-soft: #e3a3c2;
    --berry-pale: #f6dce8;
    --grey-wash: #d9d4d7;
  }
  * { margin: 0; padding: 0; box-sizing: border-box; }
  html, body {
    width: 849px;
    height: 1200px;
    overflow: hidden;
    background: var(--backdrop);
  }
  .label {
    position: relative;
    width: 849px;
    height: 1200px;
    background: var(--paper);
  }
  .brand-name {
    position: absolute;
    top: 215px;
    left: 0;
    width: 100%;
    text-align: center;
    font-family: "Tinos", "Times New Roman", serif;
    font-weight: 400;
    font-size: 150px;
    line-height: 1;
    letter-spacing: 1px;
    color: var(--ink);
  }
  .grape-artwork {
    position: absolute;
    top: 420px;
    left: 80px;
    width: 720px;
    height: 620px;
    border-radius: 46% 54% 42% 58% / 52% 40% 60% 48%;
    background:
      radial-gradient(ellipse at 40% 55%, var(--berry) 0%, var(--berry-soft) 38%, transparent 70%),
      radial-gradient(ellipse at 70% 30%, var(--berry-soft) 0%, var(--berry-pale) 45%, transparent 75%),
      radial-gradient(ellipse at 35% 85%, var(--grey-wash) 0%, transparent 55%),
      var(--berry-pale);
  }
  .varietal {
    position: absolute;
    top: 1058px;
    left: 0;
    width: 100%;
    text-align: center;
    font-family: "Tinos", "Times New Roman", serif;
    font-size: 66px;
    line-height: 1;
    color: var(--ink);
  }
  .appellation {
    position: absolute;
    top: 1132px;
    left: 0;
    width: 100%;
    text-align: center;
    font-family: "Open Sans", Arial, sans-serif;
    font-size: 30px;
    line-height: 1;
    color: var(--ink);
  }
</style>
</head>
<body>
  <main class="label">
    <h1 class="brand-name">Morival</h1>
    <div class="grape-artwork" role="img" aria-label="Ink sketch of a grape bunch with vine leaves over a pink watercolour splash"></div>
    <p class="varietal">SAUVIGNON BLANC</p>
    <p class="appellation">Val De Loire</p>
  </main>
</body>
</html>
```